Veldmark Supplies Business Card

Professional business card that stand out to our potential customers. Front and back with clean modern design

Industry/Entity Type

Oil and gas

Contact Information for Business Card

Name, address, website , office phone and cell number

Requirements
Must have
• Editable files for each employee

```html
<!DOCTYPE html>
<html lang="en">
<head>
<meta charset="utf-8">
<title>Veldmark Supplies Business Card</title>
<link rel="stylesheet" href="https://fonts.googleapis.com/css2?family=Poppins:wght@400;500;600;700&display=swap">
<style>
  :root {
    --page: #e3e7e8;
    --card-dark: #222226;
    --card-deep: #18181b;
    --pattern-light: #8e8e92;
    --brand-red: #e92626;
    --brand-blue: #12b3d4;
    --mark-dark: #111113;
    --white: #ffffff;
  }
  * { margin: 0; padding: 0; box-sizing: border-box; }
  html, body {
    width: 1200px;
    height: 960px;
    overflow: hidden;
    background: var(--page);
    font-family: "Poppins", sans-serif;
  }
  .card {
    position: absolute;
    left: 249px;
    width: 702px;
    height: 400px;
    overflow: hidden;
    background: var(--card-dark);
  }
  .card--front { top: 60px; }
  .card--back { top: 500px; }

  /* Front */
  .front-pattern {
    position: absolute;
    inset: 0;
    background:
      radial-gradient(ellipse 75% 85% at 100% 0%, var(--pattern-light) 0%, #4a4a4e 38%, rgba(34,34,38,0) 75%),
      linear-gradient(160deg, var(--card-dark) 0%, var(--card-deep) 100%);
  }
  .front-brand {
    position: absolute;
    left: 560px;
    top: 300px;
    display: flex;
    align-items: center;
    gap: 5px;
  }
  .front-brand__square {
    width: 9px;
    height: 9px;
    background: var(--brand-red);
  }
  .front-brand__name {
    font-size: 10px;
    font-weight: 600;
    color: var(--white);
    letter-spacing: 0.04em;
    text-transform: uppercase;
  }

  /* Back */
  .back-brand {
    position: absolute;
    left: 0;
    right: 0;
    top: 130px;
    display: flex;
    justify-content: center;
    align-items: center;
    gap: 10px;
  }
  .back-brand__square {
    width: 22px;
    height: 22px;
    background: var(--brand-red);
  }
  .back-brand__name {
    font-size: 26px;
    font-weight: 700;
    color: var(--white);
    letter-spacing: 0.06em;
    text-transform: uppercase;
  }
  .contact-band {
    position: absolute;
    left: 0;
    top: 224px;
    width: 100%;
    height: 113px;
    background: linear-gradient(90deg, var(--brand-blue) 0 346px, var(--brand-red) 346px 100%);
  }
  .band-mark {
    position: absolute;
    left: 306px;
    top: 218px;
    width: 88px;
    height: 120px;
    background: var(--mark-dark);
  }
  .person {
    position: absolute;
    right: 410px;
    top: 248px;
    text-align: right;
  }
  .person__name {
    font-size: 31px;
    line-height: 1;
    color: var(--brand-red);
    font-weight: 400;
    white-space: nowrap;
  }
  .person__name strong { font-weight: 700; }
  .person__title {
    margin-top: 6px;
    font-size: 17px;
    color: var(--white);
    font-weight: 500;
  }
  .contact-list {
    position: absolute;
    left: 414px;
    top: 236px;
    list-style: none;
  }
  .contact-list li {
    display: flex;
    align-items: center;
    gap: 10px;
    height: 23px;
    font-size: 17px;
    color: var(--white);
    white-space: nowrap;
  }
  .contact-list svg {
    width: 16px;
    height: 16px;
    flex: none;
    fill: none;
    stroke: var(--white);
    stroke-width: 1.8;
  }
  .address {
    position: absolute;
    left: 0;
    right: 0;
    top: 357px;
    text-align: center;
    font-size: 17px;
    color: var(--brand-red);
  }
</style>
</head>
<body>
  <section class="card card--front">
    <div class="front-pattern" role="img" aria-label="Repeating brand mark pattern fading from silver at top right to dark"></div>
    <div class="front-brand">
      <span class="front-brand__square"></span>
      <span class="front-brand__name">Veldmark Supplies</span>
    </div>
  </section>

  <section class="card card--back">
    <div class="back-brand">
      <span class="back-brand__square"></span>
      <span class="back-brand__name">Veldmark Supplies</span>
    </div>

    <div class="contact-band"></div>
    <div class="band-mark"></div>

    <div class="person">
      <p class="person__name"><strong>Marta</strong> Kovalenko</p>
      <p class="person__title">Co-Founder &amp; CEO</p>
    </div>

    <ul class="contact-list">
      <li>
        <svg viewBox="0 0 24 24"><path d="M5 3h4l2 5-3 2a11 11 0 0 0 6 6l2-3 5 2v4a2 2 0 0 1-2 2A18 18 0 0 1 3 5a2 2 0 0 1 2-2z"/></svg>
        (817) 555-0148
      </li>
      <li>
        <svg viewBox="0 0 24 24"><rect x="6" y="2" width="12" height="20" rx="2"/><path d="M11 18h2"/></svg>
        (555) 010-4372
      </li>
      <li>
        <svg viewBox="0 0 24 24"><circle cx="12" cy="12" r="10"/><path d="M2 12h20M12 2a15 15 0 0 1 0 20M12 2a15 15 0 0 0 0 20"/></svg>
        www.veldmarksupplies.com
      </li>
      <li>
        <svg viewBox="0 0 24 24"><rect x="2" y="5" width="20" height="14" rx="1"/><path d="M2 6l10 7 10-7"/></svg>
        info@veldmarksupplies.com
      </li>
    </ul>

    <p class="address">4180 Halden Rd. Suite 310 Fort Worth, TX 76107</p>
  </section>
</body>
</html>
```